Professional and creative business card design for recruiting service providers

Our company supports German medium-sized companies in filling vacancies promptly. For this we use social media marketing and bring our customers into the visibility.

We want a professional but also creative design for our business cards.

Please look at lindqvar-staff.de to get an impression of our CI.

Target Market(s)

Small and medium-sized companies in Germany from the industry

Industry/Entity Type

Industrie, Handwerk

Contact Information for Business Card

Name, Position, Telefonnummer, Email, Website

Colors
EE7325
F08F49
F5BC92
FAE3D3
FDF4ED

Requirements
Must have
• A picture of the employee and in the style of www.lindqvar-staff.de

```html
<!DOCTYPE html>
<html lang="en">
<head>
<meta charset="UTF-8">
<title>Lindqvar &amp; Staff – Business Card</title>
<link href="https://fonts.googleapis.com/css2?family=Montserrat:wght@700&family=Questrial&display=swap" rel="stylesheet">
<style>
  :root {
    --brand-orange: #EE7325;
    --brand-orange-soft: #F08F49;
    --ink: #0a0a0a;
    --paper: #ffffff;
    --stage: #ecebe8;
    --photo-light: #d9d6d2;
    --photo-dark: #4a4d52;
  }
  * { margin: 0; padding: 0; box-sizing: border-box; }
  html, body {
    width: 1200px; height: 900px; overflow: hidden;
    background: var(--stage);
  }
  .stage { position: relative; width: 1200px; height: 900px; }
  .card {
    position: absolute; left: 250px; width: 700px; height: 400px;
    overflow: hidden;
    box-shadow: 0 10px 30px rgba(0,0,0,0.18);
  }
  .card--front { top: 40px; background: var(--paper); }
  .card--back { top: 460px; background: var(--ink); }

  /* Front */
  .portrait {
    position: absolute; left: 455px; top: 22px; width: 225px; height: 330px;
    background: linear-gradient(180deg, var(--photo-light) 0%, #b9a89a 30%, var(--photo-dark) 70%, #2f3236 100%);
    border-radius: 110px 110px 0 0;
  }
  .card-wave { position: absolute; inset: 0; width: 700px; height: 400px; }
  .person { position: absolute; left: 58px; top: 58px; }
  .person__name {
    font-family: 'Montserrat', sans-serif; font-weight: 700;
    font-size: 27px; letter-spacing: 0.5px; color: var(--ink);
    line-height: 1.05;
  }
  .person__role {
    font-family: 'Questrial', sans-serif;
    font-size: 19px; color: var(--brand-orange); letter-spacing: 0.5px;
  }
  .company {
    position: absolute; left: 100px; top: 140px;
    display: flex; align-items: center; gap: 16px;
  }
  .company__mark { width: 44px; height: 44px; background: var(--brand-orange); }
  .company__name {
    font-family: 'Montserrat', sans-serif; font-weight: 700;
    font-size: 25px; line-height: 1.05; letter-spacing: 1.5px;
    color: var(--ink); text-transform: uppercase;
  }
  .contact {
    position: absolute; left: 108px; top: 222px;
    list-style: none;
    font-family: 'Questrial', sans-serif; font-size: 18px; color: var(--ink);
  }
  .contact__item {
    display: flex; align-items: center; gap: 12px; margin-bottom: 6px;
  }
  .contact__icon { width: 20px; height: 20px; flex: none; }
  .website {
    position: absolute; right: 34px; bottom: 30px;
    font-family: 'Questrial', sans-serif; font-size: 18px;
    color: var(--paper); letter-spacing: 0.5px;
  }

  /* Back */
  .back-brand {
    position: absolute; left: 50%; top: 50%;
    transform: translate(-50%, -50%);
    display: flex; align-items: center; gap: 22px;
  }
  .back-brand__mark { width: 64px; height: 64px; background: var(--brand-orange); }
  .back-brand__name {
    font-family: 'Montserrat', sans-serif; font-weight: 700;
    font-size: 36px; line-height: 1.05; letter-spacing: 2px;
    color: var(--paper); text-transform: uppercase;
  }
</style>
</head>
<body>
<main class="stage">

  <section class="card card--front" aria-label="Business card front">
    <div class="portrait" role="img" aria-label="Portrait photo of the employee in a dark suit jacket and white shirt"></div>

    <svg class="card-wave" viewBox="0 0 700 400" aria-hidden="true">
      <path d="M0,330 C200,334 390,302 540,225 C390,314 200,348 0,348 Z" fill="var(--brand-orange)"/>
      <path d="M0,360 C220,360 410,307 550,225 C610,190 660,162 700,150 L700,400 L0,400 Z" fill="var(--ink)"/>
    </svg>

    <div class="person">
      <h1 class="person__name">HENRIK ALBERS</h1>
      <p class="person__role">Managing Director</p>
    </div>

    <div class="company">
      <span class="company__mark" aria-hidden="true"></span>
      <p class="company__name">Lindqvar<br>&amp; Staff</p>
    </div>

    <ul class="contact">
      <li class="contact__item">
        <svg class="contact__icon" viewBox="0 0 24 24" aria-hidden="true">
          <path d="M6.6 10.8a15.1 15.1 0 0 0 6.6 6.6l2.2-2.2a1 1 0 0 1 1-.25 11.4 11.4 0 0 0 3.6.57 1 1 0 0 1 1 1V20a1 1 0 0 1-1 1A17 17 0 0 1 3 4a1 1 0 0 1 1-1h3.5a1 1 0 0 1 1 1c0 1.25.2 2.45.57 3.57a1 1 0 0 1-.25 1Z" fill="var(--brand-orange)"/>
        </svg>
        <span>044-987 654 321</span>
      </li>
      <li class="contact__item">
        <svg class="contact__icon" viewBox="0 0 24 24" aria-hidden="true">
          <rect x="2" y="5" width="20" height="14" fill="none" stroke="var(--brand-orange)" stroke-width="2"/>
          <path d="M2 5l10 8 10-8" fill="none" stroke="var(--brand-orange)" stroke-width="2"/>
        </svg>
        <span>info@lindqvar-staff.de</span>
      </li>
    </ul>

    <p class="website">www.lindqvar-staff.de</p>
  </section>

  <section class="card card--back" aria-label="Business card back">
    <div class="back-brand">
      <span class="back-brand__mark" aria-hidden="true"></span>
      <p class="back-brand__name">Lindqvar<br>&amp; Staff</p>
    </div>
  </section>

</main>
</body>
</html>
```